I am looking for a bottle design for a new start-up olive oil & balsamic vinegar retail store.
I am a specialty store specializing in extra virgin olive oils/infused olive oil and aged and infused balsamic vinegars.
I would like to see designs that celebrate life/food & especially superior olive oil along with the edginess & artistic community of Williamsburg, Brooklyn, New York where my store will be located.
The bottle design must be 1 color (can be white) over a dark green bottle. Bottle sizes are 200ml/375ml/750ml

Artwork design dimensions:
(front or back)

200ml
Maximum width – 2.50 inches
Maximum height – 4.25 inches

375ml
Maximum width – 3.25 inches
Maximum height – 4.50 inches

750ml
Maximum width – 3.625 inches
Maximum height – 6.50 inches

Delivery:
Adobe Illustrator or EPS file delivery.
Updates

Designers. This will not be on a paper label but screened onto a dark green bottle.

No backgrounds needed.

Thanks,
Fennel Crate

Target Market(s)

Foodies/hipsters/People who eat healthy & locally

Industry/Entity Type

Retail

Requirements
Must have
• The bottle have the following information on the front.

FENNEL
CRATE (name of store)

Pure extra virgin olive oil
&
Balsamic Vinegar

27 Harlow Lane
Williamsburg
718-552-0917
fennelcrate.com

ml/oz

On the back must have:

Supplied by
Tamsin Pantry Company
Oakland, CA
510-629-4180
Nice to have
• olives/olive trees or branches. Can be an artistic representation.
Not necessary to have image.

```html
<!DOCTYPE html>
<html lang="en">
<head>
<meta charset="utf-8">
<title>Fennel Crate – Bottle Artwork</title>
<link href="https://fonts.googleapis.com/css2?family=Federo&family=Sorts+Mill+Goudy&display=swap" rel="stylesheet">
<style>
  :root {
    --bottle-green: #4f5a14;
    --bottle-green-deep: #3c4510;
    --ink-white: #ffffff;
    --sprig-tone: rgba(255, 255, 255, 0.55);
  }
  html, body {
    margin: 0;
    padding: 0;
    width: 1200px;
    height: 900px;
    overflow: hidden;
  }
  body {
    background: var(--bottle-green);
    font-family: "Sorts Mill Goudy", Georgia, serif;
    color: var(--ink-white);
  }
  .artwork {
    position: absolute;
    top: 140px;
    width: 360px;
    height: 620px;
  }
  .artwork--front { left: 170px; }
  .artwork--back { left: 670px; }

  .wave-lines {
    position: absolute;
    inset: 0;
    width: 360px;
    height: 620px;
  }
  .wave-lines path {
    fill: none;
    stroke: var(--ink-white);
    stroke-width: 5;
    stroke-linecap: round;
  }
  .wave-lines .sprig {
    fill: var(--sprig-tone);
  }

  .product-line {
    position: absolute;
    top: 0;
    left: 0;
    width: 360px;
    text-align: center;
    font-size: 27px;
    line-height: 31px;
    margin: 0;
  }
  .store-name {
    position: absolute;
    top: 218px;
    left: 0;
    width: 360px;
    text-align: center;
    font-family: "Federo", "Sorts Mill Goudy", serif;
    margin: 0;
    font-weight: 400;
  }
  .store-name__main {
    display: block;
    font-size: 86px;
    line-height: 88px;
    letter-spacing: 2px;
  }
  .store-name__sub {
    display: block;
    font-size: 40px;
    line-height: 44px;
    letter-spacing: 7px;
  }
  .store-contact {
    position: absolute;
    top: 492px;
    left: 0;
    width: 360px;
    text-align: center;
    font-size: 19px;
    line-height: 24px;
    margin: 0;
    font-style: normal;
  }
  .volume {
    position: absolute;
    top: 572px;
    left: 0;
    width: 360px;
    text-align: center;
    font-size: 23px;
    margin: 0;
  }
  .supplier {
    position: absolute;
    top: 460px;
    left: 28px;
    font-size: 19px;
    line-height: 23px;
    margin: 0;
    font-style: normal;
  }
</style>
</head>
<body>

<section class="artwork artwork--front" aria-label="Front bottle artwork">
  <svg class="wave-lines" viewBox="0 0 360 620" aria-hidden="false">
    <path d="M0 192 C120 182, 220 125, 360 92"/>
    <path d="M0 214 C120 206, 240 155, 360 130"/>
    <rect class="sprig" x="235" y="100" width="110" height="55" rx="27" role="img" aria-label="Olive sprig drawing"/>
    <path d="M0 432 C120 422, 240 372, 360 360"/>
    <path d="M0 466 C120 452, 240 402, 360 392"/>
    <rect class="sprig" x="40" y="372" width="125" height="50" rx="25" role="img" aria-label="Olive sprig drawing"/>
  </svg>

  <p class="product-line">Pure Extra Virgin Olive oil<br>&amp;<br>Balsamic Vinegar</p>

  <h1 class="store-name">
    <span class="store-name__main">FENNEL</span>
    <span class="store-name__sub">CRATE</span>
  </h1>

  <address class="store-contact">
    27 Harlow Lane, Williamsburg<br>
    718-552-0917<br>
    fennelcrate.com
  </address>
  <p class="volume">200 ml/oz</p>
</section>

<section class="artwork artwork--back" aria-label="Back bottle artwork">
  <svg class="wave-lines" viewBox="0 0 360 620" aria-hidden="true">
    <path d="M0 100 C100 88, 200 160, 360 185"/>
    <path d="M0 122 C100 108, 200 182, 360 207"/>
    <path d="M0 352 C100 334, 220 398, 360 410"/>
    <path d="M0 372 C100 356, 220 420, 360 430"/>
  </svg>

  <address class="supplier">
    Supplied by<br>
    Tamsin Pantry Company<br>
    Oakland, CA<br>
    510-629-4180
  </address>
</section>

</body>
</html>
```